Business Cards for a law firm

Business cards for our law firm. Use our silhoette logo and OAK PARTNERS - check our website (www.oakpartners.example)

Contact Information for Business Card

our silhouette logo, OAK PARTNERS, 800-555-0147, Dorian Pemberton, dorian@oakpartners.example

Requirements
Must have
• our silhouette logo, OAK PARTNERS, 800-555-0147, Dorian Pemberton, dorian@oakpartners.example

```html
<!DOCTYPE html>
<html lang="en">
<head>
<meta charset="utf-8">
<title>Oak Partners – Business Cards</title>
<link rel="stylesheet" href="https://fonts.googleapis.com/css2?family=Inter:wght@400;500;700&family=Montserrat:wght@600&display=swap">
<style>
  :root {
    --backdrop: #808080;
    --card-dark: #1b1b1b;
    --card-light: #ffffff;
    --navy: #1f2d6b;
    --ink: #2e2e2e;
    --ink-soft: #555555;
    --mark-dim: #5c5c5c;
    --rule: #c4c4c4;
  }
  * { box-sizing: border-box; margin: 0; padding: 0; }
  html, body {
    width: 1200px; height: 1200px; overflow: hidden;
    background: var(--backdrop);
  }
  .card {
    position: absolute;
    left: 180px;
    width: 867px;
    height: 498px;
  }
  .card--front { top: 85px; background: var(--card-dark); }
  .card--back { top: 625px; background: var(--card-light); }

  .brand {
    position: absolute;
    display: flex;
    align-items: center;
    font-family: "Montserrat", sans-serif;
    font-weight: 600;
    white-space: nowrap;
  }
  .brand__square { display: block; flex: none; }
  .brand--front {
    left: 50%; top: 227px;
    transform: translateX(-50%);
    gap: 22px;
    font-size: 40px;
    letter-spacing: 3px;
    color: var(--mark-dim);
  }
  .brand--front .brand__square { width: 44px; height: 44px; background: var(--mark-dim); }
  .brand--back {
    left: 64px; top: 192px;
    gap: 14px;
    font-size: 27px;
    letter-spacing: 1.5px;
    color: var(--navy);
  }
  .brand--back .brand__square { width: 34px; height: 34px; background: var(--navy); }

  .divider {
    position: absolute;
    left: 428px; top: 155px;
    width: 1px; height: 144px;
    background: var(--rule);
  }
  .contact {
    position: absolute;
    left: 456px; top: 152px;
    font-family: "Inter", sans-serif;
  }
  .contact__name {
    font-size: 29px; font-weight: 700;
    color: var(--ink);
    letter-spacing: 0.6px;
    line-height: 1.1;
  }
  .contact__title {
    font-size: 18px; font-weight: 500;
    color: var(--ink-soft);
    letter-spacing: 2px;
    margin-top: 2px;
  }
  .contact__list { list-style: none; margin-top: 14px; }
  .contact__item {
    display: flex; align-items: center; gap: 10px;
    font-size: 19px; font-weight: 500;
    color: var(--ink-soft);
    letter-spacing: 2.2px;
    height: 30px;
  }
  .contact__icon { width: 22px; height: 22px; flex: none; }

  .address {
    position: absolute;
    left: 408px; top: 348px;
    transform: translateX(-50%);
    white-space: nowrap;
    font-family: "Inter", sans-serif;
    font-size: 19px; font-weight: 500;
    color: var(--ink-soft);
    letter-spacing: 2.2px;
  }
</style>
</head>
<body>
  <section class="card card--front">
    <div class="brand brand--front">
      <span class="brand__square"></span>
      <span class="brand__name">OAK PARTNERS</span>
    </div>
  </section>

  <section class="card card--back">
    <div class="brand brand--back">
      <span class="brand__square"></span>
      <span class="brand__name">OAK PARTNERS</span>
    </div>

    <div class="divider"></div>

    <div class="contact">
      <p class="contact__name">Dorian Pemberton</p>
      <p class="contact__title">President/Owner</p>
      <ul class="contact__list">
        <li class="contact__item">
          <svg class="contact__icon" viewBox="0 0 22 22" aria-hidden="true">
            <rect width="22" height="22" fill="var(--navy)"/>
            <path d="M8 5 L10 8 L8.6 9.4 Q10 12.6 12.6 13.4 L14 12 L17 14 L15.6 16.4 Q9 16 6 7 Z" fill="#fff"/>
          </svg>
          <span>800-555-0147</span>
        </li>
        <li class="contact__item">
          <svg class="contact__icon" viewBox="0 0 22 22" aria-hidden="true">
            <rect width="22" height="22" fill="var(--navy)"/>
            <rect x="4.5" y="6.5" width="13" height="9" fill="none" stroke="#fff" stroke-width="1.4"/>
            <path d="M4.5 6.5 L11 12 L17.5 6.5 M4.5 15.5 L9 11 M17.5 15.5 L13 11" fill="none" stroke="#fff" stroke-width="1.2"/>
          </svg>
          <span>dorian@oakpartners.example</span>
        </li>
        <li class="contact__item">
          <svg class="contact__icon" viewBox="0 0 22 22" aria-hidden="true">
            <rect width="22" height="22" fill="var(--navy)"/>
            <circle cx="11" cy="11" r="6.5" fill="none" stroke="#fff" stroke-width="1.4"/>
            <ellipse cx="11" cy="11" rx="2.8" ry="6.5" fill="none" stroke="#fff" stroke-width="1.1"/>
            <path d="M4.5 11 H17.5" stroke="#fff" stroke-width="1.1"/>
          </svg>
          <span>oakpartners.example</span>
        </li>
      </ul>
    </div>

    <p class="address">1420 Harbor View Ave #310, Lakeside, CA 90000</p>
  </section>
</body>
</html>
```